Business card for Luxury Portable Restroom Trailer company

We are a Luxury Portable Restroom Trailer Company Called FALCRIDGE HIRES. Based in Orange County California. We provide portable restroom trailers for events, such as, Weddings, Concerts, Charity events, Sporting events, Tournaments, Corporate events, ect. We rent and Sell the Luxury restrooms. Our colors are white, grey, and Orange. As you will see in the logo we uploaded.
There are 2 people in the company so the names and titles will change for the 3 people but card will remain the same. Here is the information for each Person: Dwight Penner CFO 555 318-0476
next Person: Leon Marchetti VP 555 318-0476
Next Person: Owen Marchetti CEO 555 318-0476
Information to include on the card: Luxury Restroom Trailers Rental and Sales. Weddings, Concerts, Charity, Sporting and Corp. Events.

```html
<!DOCTYPE html>
<html lang="en">
<head>
<meta charset="utf-8">
<title>Falcridge Hires — Business Card</title>
<link rel="stylesheet" href="https://fonts.googleapis.com/css2?family=Archivo:wght@400;700;800&family=Roboto:wght@400;500&display=swap">
<style>
  :root {
    --orange: #f26b22;
    --white: #ffffff;
    --grey: #5a5a5a;
    --ink: #3b3b3b;
    --backdrop: #e6e6e6;
  }
  * { box-sizing: border-box; margin: 0; padding: 0; }
  html, body { width: 1200px; height: 874px; overflow: hidden; }
  body {
    background: var(--backdrop);
    position: relative;
    font-family: "Roboto", Arial, sans-serif;
  }
  .card {
    position: absolute;
    width: 620px;
    height: 354px;
    border-radius: 22px;
    overflow: hidden;
    box-shadow: 0 10px 30px rgba(0,0,0,0.18);
  }

  /* Back of card */
  .card--back {
    left: 430px; top: 50px;
    background: var(--orange);
    color: var(--white);
  }
  .brand-mark {
    position: absolute;
    left: 50%; top: 58px;
    transform: translateX(-50%);
    width: 176px; height: 176px;
    border: 7px solid var(--white);
    border-radius: 50%;
    display: flex; align-items: center; justify-content: center;
    text-align: center;
    font-family: "Archivo", Arial, sans-serif;
    font-weight: 800;
    font-size: 22px;
    line-height: 1.15;
    letter-spacing: 1px;
  }
  .services {
    position: absolute;
    left: 0; right: 0; bottom: 40px;
    text-align: center;
    font-size: 15px;
    line-height: 1.45;
  }

  /* Front of card */
  .card--front {
    left: 150px; top: 470px;
    background: var(--white);
  }
  .logo-panel {
    position: absolute;
    left: 0; top: 0; bottom: 0;
    width: 300px;
    display: flex; align-items: center; justify-content: center;
  }
  .logo-name {
    font-family: "Archivo", Arial, sans-serif;
    font-weight: 800;
    font-size: 30px;
    line-height: 1.05;
    color: var(--orange);
    text-align: center;
    letter-spacing: 1px;
  }
  .divider {
    position: absolute;
    left: 300px; top: 0; bottom: 0;
    width: 8px;
    background: var(--grey);
  }
  .contact-panel {
    position: absolute;
    left: 308px; right: 0; top: 0; bottom: 0;
    background: var(--orange);
    color: var(--white);
    padding: 112px 0 0 40px;
  }
  .person-name {
    font-family: "Archivo", Arial, sans-serif;
    font-weight: 700;
    font-size: 26px;
    letter-spacing: 0.5px;
    text-transform: uppercase;
  }
  .person-title {
    font-size: 15px;
    margin-top: 2px;
    margin-bottom: 22px;
  }
  .contact-list { list-style: none; }
  .contact-list li {
    display: flex; align-items: center; gap: 10px;
    font-size: 17px;
    line-height: 1.45;
  }
  .contact-list svg { width: 14px; height: 14px; flex: none; fill: var(--white); }
</style>
</head>
<body>

  <section class="card card--back" aria-label="Card back">
    <div class="brand-mark">FALCRIDGE<br>HIRES</div>
    <p class="services">
      Luxury Restroom Trailers Rental and Sales.<br>
      Weddings • Concerts • Charity • Sporting and Corp. Events
    </p>
  </section>

  <section class="card card--front" aria-label="Card front">
    <div class="logo-panel">
      <p class="logo-name">FALCRIDGE<br>HIRES</p>
    </div>
    <div class="divider"></div>
    <div class="contact-panel">
      <h1 class="person-name">Dwight Penner</h1>
      <p class="person-title">CFO</p>
      <ul class="contact-list">
        <li>
          <svg viewBox="0 0 16 16" aria-hidden="true"><path d="M3.5 1 6 3.5 4.6 5.6c.8 2 2.8 4 4.8 4.8L11.5 9 15 11.5 13.2 14.6C7 14.6 1.4 9 1.4 2.8z"/></svg>
          555 318-0476
        </li>
        <li>
          <svg viewBox="0 0 16 16" aria-hidden="true"><path d="M1 3h14v10H1zM2.3 4.2 8 8.6l5.7-4.4z" fill-rule="evenodd"/></svg>
          info@falcridgehires.com
        </li>
        <li>
          <svg viewBox="0 0 16 16" aria-hidden="true"><path d="M8 1a7 7 0 1 0 0 14A7 7 0 0 0 8 1zm0 1.5c.9 0 1.9 2 2.1 4.7H5.9C6.1 4.5 7.1 2.5 8 2.5zM2.6 8.8h1.8c.1 1.5.4 2.9.9 3.9A5.5 5.5 0 0 1 2.6 8.8zm0-1.6a5.5 5.5 0 0 1 2.7-3.9c-.5 1-.8 2.4-.9 3.9zm3.3 1.6h4.2c-.2 2.7-1.2 4.7-2.1 4.7s-1.9-2-2.1-4.7zm5.7 0h1.8a5.5 5.5 0 0 1-2.7 3.9c.5-1 .8-2.4.9-3.9zm0-1.6c-.1-1.5-.4-2.9-.9-3.9a5.5 5.5 0 0 1 2.7 3.9z"/></svg>
          www.falcridgehires.com
        </li>
      </ul>
    </div>
  </section>

</body>
</html>
```